Falkrin homes and renovations business card design.

Would like some new card designs utilizing my new logo that look professional. I am open to different colors on the logo or utilize the same ones we have. I like the original concept but would like to see some fresh ideas and build on what we have already done.

Target Market(s)

Custom home building industry, Real estate sales, Renovation projects.

Industry/Entity Type

Home Builder

Contact Information for Business Card

Falkrin Homes and Renovations
2871 96th Avenue
Frank, Alberta
T2R3W8
Home : 403- 718-4063 Cell: 403- 294-5170

My info is : Dax Falkrin, President and CEO
email: falkrinhomes@maildrop-example.net
Website: falkrinhomes-example.com
websit

Requirements
Must have
• Must Use my new logo design. I am open to different colors on the logo or utilize the same ones in the existing design. I can upload the original logo design if needed.

```html
<!DOCTYPE html>
<html lang="en">
<head>
<meta charset="utf-8">
<title>Falkrin Homes and Renovations – Business Card</title>
<link rel="stylesheet" href="https://fonts.googleapis.com/css2?family=Open+Sans:wght@400;600;700&display=swap">
<style>
  :root {
    --backdrop: #e6e3de;
    --card-black: #000000;
    --gold: #bc8c26;
    --gold-text: #c3922a;
    --yellow: #f7c400;
    --light-text: #e4e4e4;
    --rule: #8a8a8a;
    --white: #ffffff;
  }
  * { margin: 0; padding: 0; box-sizing: border-box; }
  html, body {
    width: 1200px; height: 987px; overflow: hidden;
    background: var(--backdrop);
    font-family: "Open Sans", Arial, sans-serif;
  }
  .canvas { position: relative; width: 1200px; height: 987px; }
  .card {
    position: absolute; left: 293px; width: 615px; height: 351px;
    box-shadow: 0 3px 8px rgba(0,0,0,0.25);
    overflow: hidden;
  }
  .card-front { top: 130px; background: var(--card-black); }
  .card-back { top: 506px; height: 350px; background: var(--gold); }

  .brand {
    position: absolute; right: 23px; top: 96px; text-align: right;
    color: var(--gold-text); font-weight: 400; line-height: 1;
  }
  .brand-name { display: block; font-size: 38px; letter-spacing: 1px; }
  .brand-tagline { display: block; font-size: 13px; letter-spacing: 1px; margin-top: 8px; }

  .person { position: absolute; left: 33px; top: 164px; }
  .person-name { color: var(--gold-text); font-size: 23px; font-weight: 700; letter-spacing: 0.5px; line-height: 1; }
  .person-title { color: var(--light-text); font-size: 17px; margin-top: 7px; line-height: 1; }

  .divider { position: absolute; left: 33px; top: 221px; width: 559px; height: 1px; background: var(--rule); }

  .contact-list { position: absolute; left: 33px; top: 229px; list-style: none; }
  .contact-list li {
    display: flex; align-items: center; gap: 10px;
    color: var(--light-text); font-size: 16px; height: 23.5px;
  }
  .contact-list svg { width: 15px; height: 15px; flex: none; }

  .address {
    position: absolute; right: 23px; top: 232px; text-align: right;
    color: var(--light-text); font-size: 16px; line-height: 20.5px; font-style: normal;
  }

  .footer-band { position: absolute; left: 0; bottom: 0; width: 615px; height: 36px; }
  .footer-url {
    position: absolute; right: 23px; bottom: 7px;
    color: var(--white); font-size: 16.5px; line-height: 22px;
  }

  .back-brand {
    position: absolute; left: 445px; top: 190px; transform: translateX(-50%);
    text-align: center; color: var(--white); font-weight: 400; line-height: 1; white-space: nowrap;
  }
  .back-brand .brand-name { font-size: 36px; }
  .back-brand .brand-tagline { font-size: 12px; margin-top: 8px; }
  .back-url {
    position: absolute; left: 445px; top: 295px; transform: translateX(-50%);
    color: var(--white); font-size: 16px; white-space: nowrap;
  }
</style>
</head>
<body>
<main class="canvas">
  <section class="card card-front" aria-label="Card front">
    <div class="brand">
      <span class="brand-name">FALKRIN</span>
      <span class="brand-tagline">HOMES AND RENOVATIONS</span>
    </div>

    <div class="person">
      <p class="person-name">DAX FALKRIN</p>
      <p class="person-title">President and CEO</p>
    </div>

    <div class="divider"></div>

    <ul class="contact-list">
      <li>
        <svg viewBox="0 0 16 16" aria-hidden="true"><path fill="#c3922a" d="M3.5 1.5l2.5 0 1 3.5-1.6 1.2c.8 1.8 2.1 3.1 3.9 3.9L10.5 8.5l3.5 1v2.5c0 1-1 2-2 2C6.5 14 2 9.5 1.5 4c0-1 1-2.5 2-2.5z"/></svg>
        <span>403- 718-4063</span>
      </li>
      <li>
        <svg viewBox="0 0 16 16" aria-hidden="true"><rect x="4" y="1" width="8" height="14" rx="1.5" fill="none" stroke="#c3922a" stroke-width="1.6"/><rect x="7" y="12" width="2" height="1.3" fill="#c3922a"/></svg>
        <span>403- 294-5170</span>
      </li>
      <li>
        <svg viewBox="0 0 16 16" aria-hidden="true"><rect x="1" y="4" width="14" height="9" fill="#c3922a"/><path d="M1 4l7 5 7-5" fill="none" stroke="#000" stroke-width="1.2"/></svg>
        <span>falkrinhomes@maildrop-example.net</span>
      </li>
    </ul>

    <address class="address">
      Falkrin homes &amp; Renovations<br>
      2871 96th Avenue<br>
      Frank, Alberta, T2R3W8
    </address>

    <svg class="footer-band" viewBox="0 0 615 36" preserveAspectRatio="none" aria-hidden="true">
      <path d="M0 17 H352 Q362 17 362 23 L362 24 H0 Z" fill="#f7c400"/>
      <path d="M0 26 H360 Q358 28 352 28 H0 Z" fill="#3a3a3a"/>
      <path d="M355 36 Q364 36 366 26 L369 8 Q371 0 380 0 H615 V36 Z" fill="#bc8c26"/>
    </svg>
    <span class="footer-url">falkrinhomes-example.com</span>
  </section>

  <section class="card card-back" aria-label="Card back">
    <div class="back-brand">
      <span class="brand-name">FALKRIN</span>
      <span class="brand-tagline">HOMES AND RENOVATIONS</span>
    </div>
    <span class="back-url">www.falkrinhomes-example.com</span>
  </section>
</main>
</body>
</html>
```